Property development business card design

New build residential property developers. I want a professional look but customer friendly so not too corporate. I'm not sure what logo will look best so open to designs with either. Thank you

Also i don't want both names on one card its 2 names for 2 different cards but with the same design.

Industry/Entity Type

Residential

Contact Information for Business Card

KTR Developments Ltd,
58 Fennel Lane,
Ipswich,
Suffolk,
IP7 4WD

Property Research Manager
Morven Tadlock

Managing Director
Dilan Perriwick

```html
<!DOCTYPE html>
<html lang="en">
<head>
<meta charset="utf-8">
<title>KTR Developments – Business Cards</title>
<link rel="stylesheet" href="https://fonts.googleapis.com/css2?family=Open+Sans:ital,wght@0,400;0,600;0,700;1,400&display=swap">
<style>
  :root{
    --stage:#d6d6d6;
    --card:#ffffff;
    --brand-blue:#2a86c8;
    --brand-green:#8dc63f;
    --ink:#333333;
    --muted:#8c8c8c;
    --pill:#8f8f8f;
    --white:#ffffff;
  }
  *{box-sizing:border-box;margin:0;padding:0}
  html,body{width:1200px;height:894px;overflow:hidden;background:var(--stage)}
  body{font-family:"Open Sans",Arial,sans-serif;color:var(--ink)}
  .stage{position:relative;width:1200px;height:894px}
  .card{position:absolute;left:250px;width:700px;height:400px;background:var(--card);
        box-shadow:0 2px 8px rgba(0,0,0,.12);overflow:hidden}
  .card--front{top:30px}
  .card--back{top:464px}

  /* brand lockup */
  .brand{position:absolute;display:flex;align-items:center;gap:18px}
  .brand__mark{width:110px;height:110px;border-radius:50%;background:var(--brand-blue);flex:none}
  .brand__name{font-weight:600;color:var(--muted);letter-spacing:3px;text-transform:uppercase;font-size:26px}
  .card--front .brand{left:44px;top:36px}

  .person{position:absolute;left:44px;top:196px}
  .person__name{font-size:27px;font-weight:700;color:var(--ink)}
  .person__sep{font-weight:700;margin:0 8px}
  .person__role{font-size:18px;font-style:italic;font-weight:400;color:var(--ink)}
  .person__address{margin-top:8px;font-size:15px;font-weight:700;color:var(--ink)}

  .contact-band{position:absolute;left:0;top:300px;width:640px;height:46px;background:var(--brand-blue);
                border-radius:0 23px 23px 0;display:flex;align-items:center;gap:26px;padding-left:30px}
  .contact{display:flex;align-items:center;gap:8px;color:var(--white);font-size:16px}
  .contact__icon{width:20px;height:20px;border-radius:50%;background:var(--white);display:flex;align-items:center;justify-content:center}
  .contact__icon svg{width:12px;height:12px;fill:var(--brand-blue)}

  /* back */
  .web-pill{position:absolute;left:0;top:60px;width:330px;height:40px;background:var(--pill);
            border-radius:0 20px 20px 0;color:var(--white);font-size:16px;letter-spacing:2px;
            display:flex;align-items:center;padding-left:30px}
  .card--back .brand{right:60px;top:135px;flex-direction:column;gap:12px}
  .card--back .brand__mark{width:130px;height:130px}
  .card--back .brand__name{font-size:20px}
</style>
</head>
<body>
<main class="stage">

  <section class="card card--front" aria-label="Business card front">
    <div class="brand">
      <span class="brand__mark" aria-hidden="true"></span>
      <span class="brand__name">KTR Developments</span>
    </div>

    <div class="person">
      <p class="person__name">Dilan Perriwick<span class="person__sep">|</span><span class="person__role">President &amp; Ceo</span></p>
      <p class="person__address">58 Fennel Lane, Ipswich IP7 4WD</p>
    </div>

    <div class="contact-band">
      <span class="contact">
        <span class="contact__icon"><svg viewBox="0 0 24 24"><path d="M6.6 10.8a15 15 0 0 0 6.6 6.6l2.2-2.2c.3-.3.7-.4 1-.2 1.1.4 2.3.6 3.6.6.6 0 1 .4 1 1V20c0 .6-.4 1-1 1A17 17 0 0 1 3 4c0-.6.4-1 1-1h3.5c.6 0 1 .4 1 1 0 1.3.2 2.5.6 3.6.1.3 0 .7-.2 1z"/></svg></span>
        014 736 2958
      </span>
      <span class="contact">
        <span class="contact__icon"><svg viewBox="0 0 24 24"><path d="M6.6 10.8a15 15 0 0 0 6.6 6.6l2.2-2.2c.3-.3.7-.4 1-.2 1.1.4 2.3.6 3.6.6.6 0 1 .4 1 1V20c0 .6-.4 1-1 1A17 17 0 0 1 3 4c0-.6.4-1 1-1h3.5c.6 0 1 .4 1 1 0 1.3.2 2.5.6 3.6.1.3 0 .7-.2 1z"/></svg></span>
        014 736 2958
      </span>
      <span class="contact">
        <span class="contact__icon"><svg viewBox="0 0 24 24"><path d="M2 5h20v14H2z M2 5l10 8 10-8" /></svg></span>
        dilan@ktrdev.co.uk
      </span>
    </div>
  </section>

  <section class="card card--back" aria-label="Business card back">
    <div class="web-pill">www.ktrdevelopments.co.uk</div>
    <div class="brand">
      <span class="brand__mark" aria-hidden="true"></span>
      <span class="brand__name">KTR Developments</span>
    </div>
  </section>

</main>
</body>
</html>
```